Professional violinist needs business cards

I am trying to attract the following jobs:
-private violin lessons (primarily classical)
-performance gigs (weddings, birthday parties, funerals, etc.)
-collaborations with other artists (studio recordings, performances)

I want to communicate that I have a very high standard of excellence for my work, but I also love people and celebrations.
Values/style words I like are:
love, joy, peace, fun, beauty, authenticity, excellence, warmth, refined/sleek, free spirited. If that's too confusing, just ignore :)

I will attach my favorite business card template that I could find on Canva. The lines are supposed to be like a music staff, which I think is really cool, but I also don't want it to look too busy. I like the simple black and white--I think it looks sharp--but I also am open to other ideas. I also have seen business cards with pictures included that looked great, so I attached an image that could be used as well.

I am also attaching a file that I made of my initials that could be used as a logo, but I'm not sure if it should be included.

Information on the card:
-My name (18 letters total)
-"violinist"
-phone number, email, website

Thank you!

```html
<!DOCTYPE html>
<html lang="en">
<head>
<meta charset="utf-8">
<title>Caroline Westbrook — Violinist business card</title>
<link href="https://fonts.googleapis.com/css2?family=Dancing+Script:wght@500&family=Cormorant+Garamond:wght@500&family=Lora:wght@400&display=swap" rel="stylesheet">
<style>
  :root {
    --backdrop: #2b2b2b;
    --card: #22262b;
    --card-light: #272b31;
    --gold: #cdb992;
    --ink: #e8e8e6;
  }
  * { margin: 0; padding: 0; box-sizing: border-box; }
  html, body { width: 1200px; height: 1138px; overflow: hidden; background: var(--backdrop); }
  .canvas { position: relative; width: 1200px; height: 1138px; }

  .card {
    position: absolute;
    left: 275px;
    width: 620px;
    height: 375px;
    border-radius: 16px;
    background: radial-gradient(ellipse at 50% 35%, var(--card-light), var(--card) 70%);
    overflow: hidden;
  }
  .card--front { top: 186px; }
  .card--back { top: 608px; }

  .staff { position: absolute; left: 0; top: 0; }

  .brand-mark {
    position: absolute;
    width: 88px;
    height: 88px;
    border-radius: 50%;
    border: 3px solid var(--gold);
  }
  .card--front .brand-mark { left: 266px; top: 92px; }
  .card--back .brand-mark { left: 99px; top: 76px; }

  .name {
    position: absolute;
    font-family: "Dancing Script", cursive;
    font-weight: 500;
    color: var(--ink);
    line-height: 1;
    white-space: nowrap;
  }
  .card--front .name { left: 0; width: 620px; top: 208px; text-align: center; font-size: 44px; }

  .role {
    position: absolute;
    font-family: "Cormorant Garamond", serif;
    font-weight: 500;
    color: var(--ink);
    text-transform: uppercase;
    letter-spacing: 3px;
    line-height: 1;
    white-space: nowrap;
  }
  .card--front .role { left: 0; width: 620px; top: 258px; text-align: center; font-size: 19px; }

  .gold-rule { position: absolute; left: 0; width: 620px; height: 3px; background: var(--gold); opacity: 0.9; }
  .gold-rule--top { top: 21px; }
  .gold-rule--bottom { top: 349px; }

  .card--back .name { left: 208px; top: 82px; width: 290px; text-align: center; font-size: 41px; }
  .card--back .role-row {
    position: absolute; left: 212px; top: 127px; width: 284px;
    display: flex; align-items: center; justify-content: center; gap: 16px;
  }
  .card--back .role { position: static; font-size: 18px; }
  .role-line { width: 70px; height: 1px; background: var(--gold); opacity: 0.8; }

  .contacts {
    position: absolute; left: 0; top: 200px; width: 620px;
    text-align: center; list-style: none;
    font-family: "Lora", serif; font-size: 16.5px; line-height: 23.5px; color: var(--ink);
  }
  .contacts .accent { color: var(--gold); }
</style>
</head>
<body>
<main class="canvas">
  <section class="card card--front" aria-label="Card front">
    <svg class="staff" width="620" height="375" aria-hidden="true">
      <g stroke="rgba(255,255,255,0.09)" stroke-width="1">
        <line x1="0" y1="92" x2="610" y2="92"/>
        <line x1="0" y1="116" x2="610" y2="116"/>
        <line x1="0" y1="140" x2="610" y2="140"/>
        <line x1="0" y1="163" x2="610" y2="163"/>
      </g>
    </svg>
    <div class="brand-mark" aria-hidden="true"></div>
    <h1 class="name">Caroline Westbrook</h1>
    <p class="role">Violinist</p>
  </section>

  <section class="card card--back" aria-label="Card back">
    <div class="gold-rule gold-rule--top"></div>
    <div class="brand-mark" aria-hidden="true"></div>
    <h2 class="name">Caroline Westbrook</h2>
    <div class="role-row">
      <span class="role-line"></span>
      <p class="role">Violinist</p>
      <span class="role-line"></span>
    </div>
    <ul class="contacts">
      <li>+1 (555) 014-2380</li>
      <li>caroline@carolinewestbrook.com</li>
      <li>www.<span class="accent">carolinewestbrook</span>.com</li>
      <li>Annapolis, MD</li>
    </ul>
    <div class="gold-rule gold-rule--bottom"></div>
  </section>
</main>
</body>
</html>
```